GJ & DW Fencing Pty Ltd

We already have an existing logo created by Pixel Harbour however we have restructured to a company. We would like someone to add Pty Ltd to our business name please.

Colors

Designer to choose only greyscale colors for use in the design.

```html
<!DOCTYPE html>
<html lang="en">
<head>
<meta charset="utf-8">
<title>GJ &amp; DW Fencing Pty Ltd – Business Card</title>
<link href="https://fonts.googleapis.com/css2?family=Lato:wght@400;700;900&family=Bitter:wght@700&display=swap" rel="stylesheet">
<style>
  :root {
    --bg: #d9d9d9;
    --card-white: #ffffff;
    --card-black: #0b0b0b;
    --ink: #111111;
    --divider: #9a9a9a;
    --paper-shadow: rgba(0, 0, 0, 0.28);
  }
  * { box-sizing: border-box; margin: 0; padding: 0; }
  html, body {
    width: 1200px; height: 782px; overflow: hidden;
    background: var(--bg);
  }
  .stage {
    width: 1200px; height: 782px;
    display: flex; align-items: center; justify-content: center; gap: 60px;
  }
  .card {
    width: 525px; height: 300px;
    box-shadow: 0 6px 18px var(--paper-shadow);
    position: relative;
  }
  .card--front {
    background: var(--card-white);
    display: flex; align-items: center;
    padding: 0 34px;
  }
  .brand {
    width: 200px;
    display: flex; align-items: center; gap: 10px;
    font-family: "Lato", sans-serif; font-weight: 900;
    color: var(--ink);
    font-size: 21px; line-height: 1.1;
  }
  .brand__dot {
    flex: none; width: 26px; height: 26px; border-radius: 50%;
    background: var(--ink);
  }
  .divider {
    width: 1px; height: 96px; background: var(--divider);
    margin: 0 22px 0 12px;
  }
  .contact { font-family: "Lato", sans-serif; color: var(--ink); }
  .contact__name {
    font-family: "Bitter", serif; font-weight: 700;
    font-size: 16px; letter-spacing: 0.06em; text-transform: uppercase;
    margin-bottom: 12px;
  }
  .contact__row {
    display: flex; align-items: center; gap: 8px;
    font-size: 15px; margin-bottom: 7px;
  }
  .contact__icon {
    flex: none; width: 18px; height: 18px; border-radius: 50%;
    background: var(--ink); display: flex; align-items: center; justify-content: center;
  }
  .card--back {
    background: var(--card-black);
    display: flex; align-items: center; justify-content: center;
  }
  .brand--reverse { color: var(--card-white); width: auto; font-size: 20px; }
  .brand--reverse .brand__dot { background: var(--card-white); }
</style>
</head>
<body>
<main class="stage">
  <section class="card card--front">
    <div class="brand">
      <span class="brand__dot"></span>
      <span>GJ &amp; DW Fencing Pty Ltd</span>
    </div>
    <div class="divider"></div>
    <div class="contact">
      <p class="contact__name">Sam Carrow</p>
      <p class="contact__row">
        <span class="contact__icon">
          <svg width="10" height="10" viewBox="0 0 10 10"><path d="M2 1l2 2-1 1.2a6 6 0 0 0 2.8 2.8L7 6l2 2-1.2 1.2C4.5 9 1 5.5.8 2.2z" fill="#fff"/></svg>
        </span>044 5120947
      </p>
      <p class="contact__row">
        <span class="contact__icon">
          <svg width="10" height="8" viewBox="0 0 10 8"><rect x=".5" y=".5" width="9" height="7" fill="none" stroke="#fff"/><path d="M.5.5L5 4.5 9.5.5" fill="none" stroke="#fff"/></svg>
        </span>Gjdwfencing@mailbox.net
      </p>
      <p class="contact__row">
        <span class="contact__icon">
          <svg width="8" height="11" viewBox="0 0 8 11"><path d="M4 0a4 4 0 0 1 4 4c0 3-4 7-4 7S0 7 0 4a4 4 0 0 1 4-4z" fill="#fff"/><circle cx="4" cy="4" r="1.5" fill="#111"/></svg>
        </span>PO Box 418 Kelmore WA 6390
      </p>
    </div>
  </section>

  <section class="card card--back" role="img" aria-label="Black card back with a faint repeated company name pattern">
    <div class="brand brand--reverse">
      <span class="brand__dot"></span>
      <span>GJ &amp; DW Fencing Pty Ltd</span>
    </div>
  </section>
</main>
</body>
</html>
```